Förderverein einer Kirchengemeinde sucht Flyer-Design
Zielgruppe
Wir sind ein Förderverein einer Kirchengemeinde, der sich für die kirchenmusikalische Arbeit einsetzt.
Wir wünschen uns ein niveauvolles und zeitgemäßes/modernes Flyerdesign, das die etablierten Konzertbesucher anspricht, aber vor allem auch Menschen erreicht und überzeugt, die (noch) nichts mit Kirche zu tun haben.
Das Alter der (Haupt-) Zielgruppe (Männer und Frauen) erstreckt sich von 45 bis 70 Jahren.
Aufgabenstellung
Bei der Wahl des Formates würden wir (aus der Sicht von Laien) ein zweimal gefaltetes DIN A4 quer Format nehmen. Aber wir lassen uns gerne überraschen und sind grundsätzlich für andere Lösungen offen.
Bitte den Abschnitt für Adress- und sonstige Dateneintragungen samt Kontodaten so gestalten und platzieren, dass man ihn leicht abtrennen und verschicken kann.
Der Flyer soll Kirchenmusik als lebendig und attraktiv darstellen und neue (jüngere) Mitglieder für den Freundeskreis werben.
Lassen Sie die Bilder sprechen!!

```html
<!DOCTYPE html>
<html lang="de">
<head>
<meta charset="utf-8">
<title>Förderkreis Klangraum – Flyer</title>
<link href="https://fonts.googleapis.com/css2?family=Open+Sans:ital,wght@0,400;0,600;0,700;1,400&display=swap" rel="stylesheet">
<style>
  :root{
    --bg:#e4e4e6;
    --red:#b3121a;
    --red-dark:#7e0c12;
    --red-text:#b5121b;
    --ink:#4a4a4a;
    --ink-strong:#2b2b2b;
    --white:#ffffff;
    --paper:#fbfbfb;
  }
  *{box-sizing:border-box;margin:0;padding:0}
  html,body{width:1200px;height:900px;overflow:hidden}
  body{background:var(--bg);font-family:"Open Sans",Arial,sans-serif;color:var(--ink);position:relative}

  .sheet{position:absolute;box-shadow:0 10px 30px rgba(0,0,0,.18);overflow:hidden;background:var(--paper)}

  /* Cover */
  .cover{left:300px;top:36px;width:600px;height:340px}
  .cover-photo{position:absolute;inset:0;background:linear-gradient(100deg,#b8902e 0%,#8c8a84 18%,#c4c3bd 38%,#6f6d66 55%,#a9a7a0 70%,#3f3d39 100%)}
  .cover-title{position:absolute;left:36px;top:140px;color:var(--white);font-size:20px;font-weight:600;letter-spacing:.3px;text-shadow:0 1px 3px rgba(0,0,0,.35);white-space:nowrap}
  .cover-band{position:absolute;top:0;right:0;width:200px;height:100%;
    background:linear-gradient(160deg,var(--red) 0%,var(--red-dark) 100%);
    clip-path:polygon(30% 0,100% 0,100% 100%,0 100%)}
  .brand{position:absolute;right:20px;bottom:52px;width:150px;text-align:center;color:var(--white)}
  .brand-mark{width:44px;height:44px;background:var(--white);margin:0 auto 14px}
  .brand-name{font-size:14px;font-weight:700;letter-spacing:1.4px;line-height:1.25;text-transform:uppercase}

  /* Inner spread */
  .inside{left:40px;top:410px;width:1120px;height:450px;display:flex}
  .photo-col{display:flex;flex-direction:column}
  .photo-col.left{width:230px}
  .photo-col.right{width:290px}
  .photo{flex:1}
  .photo.horn{flex:.8;background:linear-gradient(135deg,#5a5047,#c9a54a 55%,#8a7d6e)}
  .photo.ensemble{flex:1.4;background:linear-gradient(160deg,#4f6a3a,#8a9a6a 45%,#e0c23a 80%,#5c7040)}
  .photo.brass{background:linear-gradient(180deg,#c8c8c4,#e8e6e1 45%,#3a3a3a 90%)}
  .photo.choir{flex:1.2;background:linear-gradient(180deg,#c9a89a,#dcc9b4 30%,#1e1c1c 70%,#121212)}

  .text-col{width:340px;background:var(--paper);padding:24px 24px 16px 30px}
  .intro{display:flex;gap:12px;margin-bottom:14px}
  .headline{color:var(--red-text);font-size:16px;font-weight:600;line-height:1.2;flex:0 0 124px;text-align:right;padding-right:12px;border-right:1.5px solid var(--red-text)}
  .intro p{font-size:10px;line-height:1.45;flex:1}
  .subhead{color:var(--red-text);font-size:13px;font-weight:600;margin-bottom:6px}
  .benefits{list-style:none;font-size:10.5px;line-height:1.42}
  .benefits li{margin-bottom:4px}
  .benefits strong{color:var(--ink-strong);font-weight:700}

  .reasons{width:260px;position:relative;color:var(--white);padding:38px 16px 0 36px}
  .reasons::before{content:"";position:absolute;inset:0;z-index:0;
    background:linear-gradient(170deg,var(--red-dark) 0%,var(--red) 45%,#9c0f16 100%);
    clip-path:polygon(0 0,100% 0,100% 100%,8% 100%)}
  .reasons>*{position:relative;z-index:1}
  .reasons h2{font-size:13px;font-weight:700;margin-bottom:14px;white-space:nowrap}
  .reasons .lead{font-size:11px;margin-bottom:10px}
  .reasons ul{list-style:none;font-size:11px;line-height:1.45}
  .reasons li{margin-bottom:11px}
</style>
</head>
<body>

  <section class="sheet cover">
    <div class="cover-photo" role="img" aria-label="Foto: Orgelpfeifen mit vergoldetem Schnitzwerk"></div>
    <p class="cover-title">Kirchenmusik braucht Freunde…</p>
    <div class="cover-band"></div>
    <div class="brand">
      <div class="brand-mark"></div>
      <div class="brand-name">Förderkreis<br>Klangraum</div>
    </div>
  </section>

  <section class="sheet inside">
    <div class="photo-col left">
      <div class="photo horn" role="img" aria-label="Foto: Hände an einem Waldhorn"></div>
      <div class="photo ensemble" role="img" aria-label="Foto: Flötenensemble und Kinderchor in gelben Shirts im Garten"></div>
    </div>

    <div class="text-col">
      <div class="intro">
        <h1 class="headline">Kirchenmusik braucht Freunde</h1>
        <p>Im Jahr 1999 gegründet, unterstützt der Förderkreis Klangraum die vielfältigen musikalischen Aktivitäten an der St. Martini-Kirche.<br>Wir laden Sie ein, Mitglied zu werden!</p>
      </div>
      <h3 class="subhead">Mit Ihrem Beitrag …</h3>
      <ul class="benefits">
        <li>… bereichern Sie Lindenaus kulturelle Landschaft durch den Erhalt und Ausbau unseres hohen kirchenmusikalischen Niveaus</li>
        <li>… stärken Sie das Ehrenamt</li>
        <li>… ermöglichen Sie der <strong>Kantorei</strong>, dem <strong>Posaunenchor</strong>, dem <strong>Kinderchor</strong> und dem <strong>Flötenensemble</strong> regelmäßige Probenarbeit, Probenwochenenden und die Anschaffung von Notenmaterial</li>
        <li>… erhalten Sie die historische <strong>Johann Albrecht Orgel von 1748</strong></li>
        <li>… fördern Sie die Ausbildung kirchenmusikalischen Nachwuchses</li>
      </ul>
    </div>

    <div class="photo-col right">
      <div class="photo brass" role="img" aria-label="Foto: Posaunenchor vor einem Gebäude"></div>
      <div class="photo choir" role="img" aria-label="Foto: Kantorei in schwarzer Kleidung im Kirchenraum"></div>
    </div>

    <div class="reasons">
      <h2>Mitglieder haben gute Gründe:</h2>
      <p class="lead">Sie…</p>
      <ul>
        <li>… erhalten ermäßigte Eintrittspreise von gemeindeeigenen Konzerten</li>
        <li>… können Konzertkarten vor dem öffentlichen Verkauf erwerben</li>
        <li>… gestalten die Arbeit des Förderkreises in den jährlichen Mitgliederversammlungen aktiv mit</li>
        <li>… erhalten aktuelle Informationen über Veranstaltungen der Gemeinde bequem per Email und profitieren so zu allererst</li>
        <li>… können den Mitgliedsbeitrag steuerlich absetzen und erhalten eine Spendenbescheinigung</li>
      </ul>
    </div>
  </section>

</body>
</html>
```